Classy, Elegant, Simple Business Card Design

Looking to have a classy, simple, and elegant design. Want a top notch designed business card. I really like the look of the new torvane credit card. I also like the design I attached. I am trying to reach 21-29 year old females for booking us for there wedding or event. We offer Disc Jockey Service, Photo Booth Rentals, and Uplighting .

Target Market(s)

21-28 year old females

Contact Information for Business Card

Has to have logo, website, email, and phone number

Font styles to use
Other font styles liked:
• open to font choice, modern, clean
Designer to choose
33a6d7
0791cd
0555a3
ffffff

Requirements
Must have
• Has to have logo, website, email, and phone number
Nice to have
• I really like the design of the new torvane credit card. I also included my logo and some designs I like
Should not have
• clutter or too much info

```html
<!DOCTYPE html>
<html lang="en">
<head>
<meta charset="utf-8">
<title>Marvessa Event Group – Business Card</title>
<link href="https://fonts.googleapis.com/css2?family=Questrial&family=Roboto:wght@400;700&display=swap" rel="stylesheet">
<style>
  :root {
    --backdrop: #3b3c3e;
    --card: #1e1f22;
    --sky: #33a6d7;
    --azure: #0791cd;
    --royal: #0555a3;
    --white: #ffffff;
    --muted: #9a9ca0;
  }
  * { margin: 0; padding: 0; box-sizing: border-box; }
  html, body { width: 799px; height: 1200px; overflow: hidden; }
  body {
    background: var(--backdrop);
    font-family: "Roboto", Arial, sans-serif;
    position: relative;
  }
  .card {
    position: absolute;
    left: 80px;
    width: 640px;
    height: 366px;
    background: var(--card);
    border-radius: 6px;
    overflow: hidden;
    box-shadow: 0 18px 40px rgba(0,0,0,.45);
  }
  .card--front { top: 110px; }
  .card--back  { top: 700px; }

  .brand {
    position: absolute;
    display: flex;
    align-items: center;
    gap: 14px;
    white-space: nowrap;
  }
  .brand__dot {
    width: 22px; height: 22px;
    border-radius: 50%;
    background: var(--azure);
    flex: none;
  }
  .brand__name {
    font-family: "Questrial", Arial, sans-serif;
    color: var(--azure);
    letter-spacing: 2px;
    text-transform: uppercase;
  }

  /* Front */
  .card--front .brand {
    top: 120px; left: 0; right: 0;
    justify-content: center;
  }
  .card--front .brand__name { font-size: 34px; }
  .sound-band {
    position: absolute;
    left: 0; right: 0; bottom: 0;
    height: 120px;
    background: linear-gradient(to top, rgba(7,145,205,.75), rgba(5,85,163,.15) 75%, transparent);
  }

  /* Back */
  .card--back .brand { top: 52px; left: 40px; }
  .card--back .brand__name { font-size: 28px; }
  .brand__rule {
    width: 1px; height: 40px;
    background: var(--muted);
    opacity: .6;
  }
  .person { position: absolute; top: 130px; left: 40px; }
  .person__name { color: var(--azure); font-weight: 700; font-size: 22px; }
  .person__role { color: var(--white); font-size: 14px; margin-top: 4px; }
  .contacts {
    position: absolute;
    top: 196px; left: 340px;
    list-style: none;
  }
  .contacts li {
    display: flex; align-items: center; gap: 12px;
    color: var(--white); font-size: 16px;
    margin-bottom: 9px;
  }
  .contacts svg { width: 16px; height: 16px; fill: var(--azure); flex: none; }
  .footer-band {
    position: absolute;
    left: 180px; right: 0; bottom: 0;
    height: 56px;
    background: linear-gradient(90deg, var(--royal), var(--azure));
    border-top-left-radius: 60px 56px;
    display: flex; align-items: center;
    padding-left: 60px;
    color: var(--white); font-size: 16px;
  }
</style>
</head>
<body>
  <section class="card card--front">
    <div class="brand">
      <span class="brand__dot"></span>
      <span class="brand__name">Marvessa Event Group</span>
    </div>
    <div class="sound-band" role="img" aria-label="Blue equalizer bar pattern along the bottom edge"></div>
  </section>

  <section class="card card--back">
    <div class="brand">
      <span class="brand__dot"></span>
      <span class="brand__rule"></span>
      <span class="brand__name">Marvessa Event Group</span>
    </div>
    <div class="person">
      <p class="person__name">Evan Marlow</p>
      <p class="person__role">Founder &amp; CEO</p>
    </div>
    <ul class="contacts">
      <li>
        <svg viewBox="0 0 24 24"><path d="M6.6 10.8a15.1 15.1 0 0 0 6.6 6.6l2.2-2.2a1 1 0 0 1 1-.25 11.4 11.4 0 0 0 3.6.57 1 1 0 0 1 1 1V20a1 1 0 0 1-1 1A17 17 0 0 1 3 4a1 1 0 0 1 1-1h3.5a1 1 0 0 1 1 1c0 1.25.2 2.45.57 3.57a1 1 0 0 1-.25 1z"/></svg>
        555 0142 0178
      </li>
      <li>
        <svg viewBox="0 0 24 24"><path d="M2 5h20v14H2z M2 5l10 8 10-8" fill="none" stroke="#0791cd" stroke-width="2"/></svg>
        evan@marvessaevents.com
      </li>
      <li>
        <svg viewBox="0 0 24 24"><circle cx="12" cy="12" r="9" fill="none" stroke="#0791cd" stroke-width="2"/><path d="M3 12h18M12 3c3 3 3 15 0 18M12 3c-3 3-3 15 0 18" fill="none" stroke="#0791cd" stroke-width="1.6"/></svg>
        www.marvessaevents.com
      </li>
    </ul>
    <div class="footer-band">Marvessa Event Group</div>
  </section>
</body>
</html>
```